Logo for a Food & Beverage Franchise Company

We need a logo and stationary for a new company that just aquired a restaurant franchise. We need a sleep and professional logo with stationary.

Target Market(s)

Adults, resturaunt owners, franchisors (Companies who own food franchise companies such as Farrowbys Head Office, Toastwell International Franchise)
and Big Food and Beverage who wish to give franchise rights to us)

Industry/Entity Type

Restaurant

Logo Text

Velvet Harbor

Logo styles of interest
Emblem Logo
Pictorial/Combination Logo
Character Logo
Font styles to use
Serif
Sans Serif

Colors
ffc214
f78f20
f37022
faa54b
fece3e
fbed22

Requirements
Must have
• Maximum three color. The less the better.
Nice to have
• It does not have to have a crown, but if you wish to have a crown then it does not have to be so sharp and clear. Abstract is better.

```html
<!DOCTYPE html>
<html lang="en">
<head>
<meta charset="utf-8">
<title>Velvet Harbor Stationery</title>
<link href="https://fonts.googleapis.com/css2?family=Josefin+Sans:wght@600&family=Arimo:wght@400;700&display=swap" rel="stylesheet">
<style>
  :root {
    --bg: #5a646f;
    --paper: #ffffff;
    --orange: #f89a10;
    --peach: #fde0b6;
    --ink: #1e1e1e;
    --grey-text: #444444;
    --disc-hub: #7c8187;
    --shadow: 0 6px 14px rgba(0,0,0,0.28);
  }
  * { box-sizing: border-box; margin: 0; padding: 0; }
  html, body { width: 1200px; height: 900px; overflow: hidden; }
  body {
    position: relative;
    background: var(--bg);
    font-family: "Arimo", Arial, sans-serif;
  }
  .wordmark {
    font-family: "Josefin Sans", "Montserrat", sans-serif;
    font-weight: 600;
    letter-spacing: 0.22em;
    text-transform: uppercase;
    white-space: nowrap;
    display: flex;
    align-items: center;
    gap: 6px;
  }
  .wordmark .mark-square { width: 8px; height: 8px; background: currentColor; display: inline-block; }

  .piece { position: absolute; background: var(--paper); box-shadow: var(--shadow); overflow: hidden; }

  /* Notepad */
  .notepad { left: 60px; top: 50px; width: 300px; height: 420px; }
  .notepad .top-band {
    position: absolute; left: 0; top: 0; width: 100%; height: 96px; background: var(--orange);
    display: flex; justify-content: flex-end; align-items: flex-start; padding: 16px 16px 0 0;
  }
  .notepad .top-band .wordmark { color: var(--paper); font-size: 9px; }
  .notepad .corner-mark { position: absolute; left: 18px; top: 116px; color: var(--orange); font-size: 8px; }
  .notepad .faint-name {
    position: absolute; left: 30px; top: 270px; color: var(--peach);
    font-size: 30px; transform: rotate(-40deg); transform-origin: left top; letter-spacing: 0.12em;
  }

  /* Letterhead */
  .letterhead { left: 400px; top: 50px; width: 300px; height: 420px; padding: 24px 22px; }
  .letterhead .head { display: flex; justify-content: flex-end; margin-bottom: 16px; }
  .letterhead .head .wordmark { color: var(--orange); font-size: 9px; }
  .letterhead .body { font-size: 6.6px; line-height: 1.45; color: var(--ink); }
  .letterhead .body p { margin-bottom: 7px; text-align: justify; }
  .letterhead .foot-mark { position: absolute; left: 22px; bottom: 20px; color: var(--orange); font-size: 7px; }

  /* Business cards */
  .card { left: 760px; width: 300px; height: 170px; }
  .card-front { top: 50px; }
  .card-front .mid-band {
    position: absolute; left: 0; top: 50px; width: 100%; height: 70px; background: var(--orange);
    display: flex; align-items: center; justify-content: center;
  }
  .card-front .mid-band .wordmark { color: var(--paper); font-size: 15px; }
  .card-back { top: 250px; padding: 0 22px; }
  .card-back .top-stripe { position: absolute; left: 0; top: 20px; width: 100%; height: 22px; background: var(--orange); }
  .card-back .wordmark { position: absolute; right: 22px; top: 26px; color: var(--paper); font-size: 8px; }
  .card-back .details { position: absolute; left: 22px; top: 62px; font-size: 8px; line-height: 1.6; color: var(--grey-text); }
  .card-back .details .person { font-weight: 700; color: var(--ink); font-size: 9px; }

  /* Disc */
  .disc {
    position: absolute; left: 770px; top: 500px; width: 300px; height: 300px; border-radius: 50%;
    background: var(--paper); box-shadow: var(--shadow);
  }
  .disc .hub {
    position: absolute; left: 50%; top: 50%; width: 64px; height: 64px; margin: -32px 0 0 -32px;
    border-radius: 50%; background: var(--disc-hub); border: 8px solid #b8bcc1;
  }
  .disc .hub::after {
    content: ""; position: absolute; left: 50%; top: 50%; width: 18px; height: 18px; margin: -9px 0 0 -9px;
    border-radius: 50%; background: var(--bg);
  }
  .disc .wordmark { position: absolute; left: 50%; top: 60px; transform: translateX(-50%); color: var(--orange); font-size: 9px; }
  .disc .disc-mark { position: absolute; left: 50%; bottom: 58px; width: 10px; height: 10px; margin-left: -5px; background: var(--orange); }

  /* Envelope */
  .envelope { left: 60px; top: 510px; width: 660px; height: 330px; }
  .envelope .corner-mark { position: absolute; left: 20px; top: 20px; color: var(--ink); font-size: 8px; }
  .envelope .band {
    position: absolute; left: 0; bottom: 0; width: 100%; height: 96px; background: var(--orange);
    display: flex; align-items: center; justify-content: center;
  }
  .envelope .band .wordmark { color: var(--paper); font-size: 20px; }
  .envelope .address {
    position: absolute; right: 24px; top: 24px; font-size: 9px; line-height: 1.55; color: var(--grey-text); text-align: left;
  }
</style>
</head>
<body>

  <section class="piece notepad">
    <div class="top-band"><span class="wordmark">Velvet Harbor</span></div>
    <div class="wordmark corner-mark"><span class="mark-square"></span>Velvet Harbor</div>
    <div class="wordmark faint-name">Velvet Harbor</div>
  </section>

  <section class="piece letterhead">
    <header class="head"><span class="wordmark"><span class="mark-square"></span>Velvet Harbor</span></header>
    <div class="body">
      <p>Thank you for your interest in our group. We operate and grow restaurant franchises across the region, bringing trusted kitchens to new neighbourhoods. Our teams handle site planning, staff training, supply and daily service so every partner brand is run with care and consistency.</p>
      <p>We would welcome a meeting to discuss how our experience can support your expansion plans. Our portfolio includes quick service, casual dining and cafe formats, each managed with clear reporting and shared standards.</p>
      <p>Please find our company profile enclosed. We look forward to hearing from you and building a lasting partnership.</p>
      <p>Kind regards,</p>
    </div>
    <div class="wordmark foot-mark">Velvet Harbor</div>
  </section>

  <section class="piece card card-front">
    <div class="mid-band"><span class="wordmark">Velvet Harbor</span></div>
  </section>

  <section class="piece card card-back">
    <div class="top-stripe"></div>
    <span class="wordmark">Velvet Harbor</span>
    <div class="details">
      <div class="person">Omar Haddad</div>
      <div>General Manager</div>
      <div>+974 4410 2233</div>
      <div>omar@velvetharbor.com</div>
    </div>
  </section>

  <section class="disc">
    <span class="wordmark">Velvet Harbor</span>
    <div class="hub"></div>
    <span class="disc-mark"></span>
  </section>

  <section class="piece envelope">
    <div class="wordmark corner-mark"><span class="mark-square"></span>Velvet Harbor</div>
    <address class="address">
      Office: +974 418 5560<br>
      Mobile: +971 50 276 8841<br>
      Email: info@velvetharbor.com<br>
      P.O. Box 48210, Harbor Bay<br>
      www.velvetharbor.com
    </address>
    <div class="band"><span class="wordmark">Velvet Harbor</span></div>
  </section>

</body>
</html>
```